Veltrane Group Business Card Design

The CEO is looking for a new trendy look for his business card.
You can stay with current branding or come up with something new/creative. It can be 3D, including Medical Office buildings. You can use our logo in a variety of colors. Please include name, title, company name, company website, email address, cell number

Target Market(s)

Real Estate Development and Construction

Industry/Entity Type

Health care real estate

Contact Information for Business Card

Rohesh Kamdar, CEO M-604.781.2249 E-roheshkamdar@veltrane.com Address:4180 Lindqvist Ave, Tampa, FL 33482 www.veltrane.com

Font styles to use
Other font styles liked:
• Be creative

Requirements
Must have
• Creative, trendy look
Nice to have
• Please go to our website to get a feel- www. veltrane.com
Should not have
• small fonts

```html
<!DOCTYPE html>
<html lang="en">
<head>
<meta charset="UTF-8">
<title>Veltrane Group Business Card</title>
<link href="https://fonts.googleapis.com/css2?family=Montserrat:wght@400;700;900&display=swap" rel="stylesheet">
<style>
  :root {
    --stage: #2b2b2b;
    --card-dark: #1c1c1c;
    --card-light: #ffffff;
    --ink-light: #ffffff;
    --ink-dark: #111111;
    --rule: #222222;
  }
  * { margin: 0; padding: 0; box-sizing: border-box; }
  html, body {
    width: 1200px; height: 875px; overflow: hidden;
    background: var(--stage);
    font-family: "Montserrat", sans-serif;
  }
  .stage { position: relative; width: 1200px; height: 875px; }
  .card {
    position: absolute;
    width: 520px; height: 298px;
    border-radius: 18px;
    box-shadow: 0 14px 30px rgba(0,0,0,0.45);
    overflow: hidden;
  }
  .card--front {
    left: 70px; top: 170px;
    background: var(--card-dark);
    display: flex; align-items: center; justify-content: center;
  }
  .card--front .wordmark {
    color: var(--ink-light);
    font-weight: 900;
    font-size: 50px;
    letter-spacing: -1px;
  }
  .card--back {
    left: 610px; top: 405px;
    background: var(--card-light);
    color: var(--ink-dark);
  }
  .card--back .wordmark {
    position: absolute; right: 28px; top: 30px;
    font-weight: 900; font-size: 30px; letter-spacing: -0.5px;
  }
  .card--back .header-rule {
    position: absolute; left: 28px; right: 28px; top: 84px;
    height: 1px; background: var(--rule);
  }
  .address {
    position: absolute; right: 28px; top: 100px;
    text-align: right; font-size: 11px; line-height: 1.45;
  }
  .person { position: absolute; left: 30px; top: 170px; }
  .person .name { font-weight: 700; font-size: 19px; }
  .person .title { font-size: 11px; margin-top: 2px; }
  .person .name-rule { width: 190px; height: 1px; background: var(--rule); margin: 6px 0 8px; }
  .contact-list { list-style: none; font-size: 11px; }
  .contact-list li { display: flex; align-items: center; gap: 8px; margin-bottom: 5px; }
  .contact-list svg { width: 11px; height: 11px; fill: var(--ink-dark); }
</style>
</head>
<body>
<div class="stage">
  <div class="card card--front">
    <span class="wordmark">Veltrane Group</span>
  </div>

  <div class="card card--back">
    <span class="wordmark">Veltrane Group</span>
    <div class="header-rule"></div>
    <p class="address">4180 Lindqvist Ave,<br>Tampa, FL 33482</p>
    <div class="person">
      <p class="name">Rohesh Kamdar</p>
      <p class="title">CEO</p>
      <div class="name-rule"></div>
      <ul class="contact-list">
        <li>
          <svg viewBox="0 0 24 24" aria-hidden="true"><path d="M6.6 10.8a15 15 0 0 0 6.6 6.6l2.2-2.2c.3-.3.7-.4 1-.2 1.1.4 2.3.6 3.6.6.6 0 1 .4 1 1V20c0 .6-.4 1-1 1A17 17 0 0 1 3 4c0-.6.4-1 1-1h3.5c.6 0 1 .4 1 1 0 1.3.2 2.5.6 3.6.1.3 0 .7-.2 1z"/></svg>
          <span>604.781.2249</span>
        </li>
        <li>
          <svg viewBox="0 0 24 24" aria-hidden="true"><path d="M2 5h20v14H2zM4 7v.5l8 5 8-5V7l-8 5z"/></svg>
          <span>roheshkamdar@veltrane.com</span>
        </li>
        <li>
          <svg viewBox="0 0 24 24" aria-hidden="true"><path d="M12 2a10 10 0 1 0 0 20 10 10 0 0 0 0-20zm6.9 9h-3a15 15 0 0 0-1.2-6A8 8 0 0 1 18.9 11zM12 4.1c.9 1.3 1.7 3.8 1.9 6.9h-3.8c.2-3.1 1-5.6 1.9-6.9zM9.3 5a15 15 0 0 0-1.2 6h-3A8 8 0 0 1 9.3 5zM5.1 13h3a15 15 0 0 0 1.2 6A8 8 0 0 1 5.1 13zM12 19.9c-.9-1.3-1.7-3.8-1.9-6.9h3.8c-.2 3.1-1 5.6-1.9 6.9zm2.7-.9a15 15 0 0 0 1.2-6h3a8 8 0 0 1-4.2 6z"/></svg>
          <span>www.veltrane.com</span>
        </li>
      </ul>
    </div>
  </div>
</div>
</body>
</html>
```